VFX Company Business Card Design Project

The Kestrel Works is a decentralized Visual Effects Studio servicing the television and feature film industries.
Project Brief:
Take our logo that was previously designed on Pencil Harbor and make a double sided business card.
Requirements:
- Card MUST be double sided.
- Front of card MUST have the yellow part of our logo against the dark grey background.
- Back of card is completely up to the designer.
- Back of card must include the complete company logo.
Please follow these File Preparation guidelines:
http://printnook.ca/infopage?file=filetype_en&s=PrintNook_new&lang=en
Business

```html
<!DOCTYPE html>
<html lang="en">
<head>
<meta charset="utf-8">
<title>The Kestrel Works – Business Card</title>
<link rel="stylesheet" href="https://fonts.googleapis.com/css2?family=Questrial&family=Open+Sans:ital,wght@0,400;1,700&display=swap">
<style>
  :root {
    --backdrop: #d8b08a;
    --card: #2b2b2b;
    --band: #5f6b6f;
    --yellow: #fcc72c;
    --white: #ffffff;
    --label: #1a1a1a;
    --grey-text: #c9cdd0;
  }
  * { box-sizing: border-box; margin: 0; padding: 0; }
  html, body { width: 1200px; height: 788px; overflow: hidden; }
  body {
    position: relative;
    background: var(--backdrop);
    font-family: "Questrial", "Century Gothic", sans-serif;
  }
  .side-label {
    position: absolute;
    font-family: "Open Sans", Arial, sans-serif;
    font-size: 21px;
    color: var(--label);
    text-align: center;
    width: 200px;
  }
  .card {
    position: absolute;
    width: 525px;
    height: 300px;
    background: var(--card);
    border-radius: 22px;
    overflow: hidden;
  }
  .card--back { left: 338px; top: 78px; }
  .card--front-mark { left: 54px; top: 445px; }
  .card--front-lockup { left: 622px; top: 445px; }

  .company-name {
    position: absolute;
    white-space: nowrap;
    letter-spacing: 0.5px;
  }
  .card--back .company-name {
    left: 14px; top: 120px; width: 238px;
    font-size: 24px; color: var(--white); text-align: center;
  }
  .divider {
    position: absolute;
    left: 261px; top: 86px;
    width: 2px; height: 118px;
    background: linear-gradient(to bottom, transparent, #111 20%, #111 80%, transparent);
  }
  .contact {
    position: absolute;
    left: 289px; top: 89px;
    font-family: "Open Sans", Arial, sans-serif;
    font-size: 13px;
    line-height: 19px;
    color: var(--white);
    list-style: none;
  }
  .contact li.address { line-height: 18px; }
  .contact b { font-style: italic; font-weight: 700; }
  .name-band {
    position: absolute;
    left: 0; bottom: 0;
    width: 100%; height: 38px;
    background: var(--band);
    color: var(--white);
    text-align: center;
    font-size: 19px;
    line-height: 38px;
    letter-spacing: 0.6px;
  }
  .name-band small { font-size: 13px; letter-spacing: 0.4px; }

  .card--front-mark .company-name {
    left: 0; width: 100%; top: 118px;
    text-align: center;
    font-size: 50px;
    color: var(--yellow);
  }
  .lockup {
    position: absolute;
    left: 0; width: 100%; top: 128px;
    display: flex; align-items: center; justify-content: center; gap: 18px;
  }
  .lockup .company-name { position: static; font-size: 36px; color: var(--yellow); }
  .web {
    position: absolute;
    left: 0; bottom: 20px; width: 100%;
    text-align: center;
    color: var(--white);
    font-size: 20px;
    letter-spacing: 3.2px;
  }
</style>
</head>
<body>
  <div class="side-label" style="left:500px; top:32px;">Back</div>
  <section class="card card--back">
    <div class="company-name">The Kestrel Works</div>
    <div class="divider"></div>
    <ul class="contact">
      <li><b>cell</b> 123-456-7890</li>
      <li><b>phone</b> 123-456-7890</li>
      <li><b>email</b> info@website.com</li>
      <li><b>web</b> www.website.com</li>
      <li class="address">0000#, Area Name</li>
      <li class="address">State Name, Country code</li>
    </ul>
    <div class="name-band">Your Name, <small>Designation</small></div>
  </section>

  <div class="side-label" style="left:227px; top:403px;">Front - 1</div>
  <section class="card card--front-mark">
    <div class="company-name">The Kestrel Works</div>
    <div class="web">www.website.com</div>
  </section>

  <div class="side-label" style="left:800px; top:403px;">Front - 2</div>
  <section class="card card--front-lockup">
    <div class="lockup">
      <svg width="40" height="40" viewBox="0 0 40 40" aria-hidden="true"><circle cx="20" cy="20" r="20" fill="var(--yellow)"/></svg>
      <span class="company-name">The Kestrel Works</span>
    </div>
    <div class="web">www.website.com</div>
  </section>
</body>
</html>
```